Business Card for Professional Photographer

I'm looking for an eye catching modern clean design that compliments my logo/ website fonts & colours.
I specialise in architecture, corporate & commercial photography so I'm marketing to professional clients rather than portrait / wedding clients.

I would prefer to not have a solid black design.

My logo brand guide is as follows :

Main front font. : Reislust
Main font colour : #fff
Slogan front font : Ubuntu Bold
Monogram front font : Venti Medium
Container colour : #fff

I need print ready files in pdf .png & .eps formats.

Included in the files below are some screen grabs as reference to font & colours etc.

```html
<!DOCTYPE html>
<html lang="en">
<head>
<meta charset="UTF-8">
<title>Clear Frame Studio — Business Card</title>
<link href="https://fonts.googleapis.com/css2?family=Montserrat:wght@300;400;500;700&display=swap" rel="stylesheet">
<style>
  :root {
    --page-bg: #e6e6e8;
    --gold-light: #dcae74;
    --gold-dark: #c4924f;
    --gold-text: #c9974f;
    --ink: #2a2420;
    --grey-text: #5c5c5c;
    --card-white: #ffffff;
    --mark-faint: rgba(90, 60, 25, 0.14);
  }
  * { box-sizing: border-box; margin: 0; padding: 0; }
  html, body { width: 1200px; height: 960px; overflow: hidden; }
  body {
    background: var(--page-bg);
    font-family: "Montserrat", sans-serif;
    display: flex;
    flex-direction: column;
    align-items: center;
    justify-content: center;
    gap: 56px;
  }
  .card {
    position: relative;
    width: 640px;
    height: 366px;
    border-radius: 22px;
    box-shadow: 0 10px 28px rgba(0,0,0,0.18);
    overflow: hidden;
  }

  /* Back side */
  .card-back {
    background: linear-gradient(120deg, var(--gold-dark), var(--gold-light));
  }
  .card-back .faint-square {
    position: absolute;
    left: 96px;
    top: 128px;
    width: 190px;
    height: 190px;
    border: 9px solid var(--mark-faint);
  }
  .card-back .identity {
    position: absolute;
    left: 336px;
    top: 118px;
    color: var(--ink);
  }
  .brand-name {
    font-weight: 400;
    font-size: 25px;
    letter-spacing: 3px;
    text-transform: uppercase;
    line-height: 1;
  }
  .brand-tagline {
    font-weight: 700;
    font-size: 8.5px;
    letter-spacing: 1.4px;
    margin-top: 5px;
  }
  .card-back .web {
    font-weight: 400;
    font-size: 13px;
    letter-spacing: 3px;
    margin-top: 10px;
  }

  /* Front side */
  .card-front { background: var(--card-white); }
  .front-brand {
    position: absolute;
    left: 48px;
    top: 94px;
    display: flex;
    align-items: center;
    gap: 16px;
  }
  .front-brand .plain-square {
    width: 58px;
    height: 58px;
    border: 3px solid var(--gold-text);
  }
  .front-brand .brand-name { color: var(--grey-text); font-size: 24px; }
  .front-brand .brand-tagline { color: var(--grey-text); }

  .person {
    position: absolute;
    right: 44px;
    top: 70px;
    text-align: right;
  }
  .person-name {
    color: var(--gold-text);
    font-weight: 500;
    font-size: 22px;
    letter-spacing: 0.5px;
    text-transform: uppercase;
  }
  .person-title {
    color: var(--grey-text);
    font-weight: 400;
    font-size: 15px;
    margin-top: 2px;
  }
  .address {
    color: var(--grey-text);
    font-style: normal;
    font-size: 15px;
    line-height: 1.3;
    margin-top: 18px;
  }
  .person .web {
    color: var(--gold-text);
    font-weight: 700;
    font-size: 15px;
    letter-spacing: 1px;
    margin-top: 10px;
  }

  .contacts {
    position: absolute;
    left: 48px;
    bottom: 40px;
    list-style: none;
    color: var(--grey-text);
    font-size: 16px;
    line-height: 1.3;
  }
</style>
</head>
<body>
  <section class="card card-back" aria-label="Card back">
    <div class="faint-square"></div>
    <div class="identity">
      <div class="brand-name">Clear Frame Studio</div>
      <div class="brand-tagline">Architecture Corporate Commercial</div>
      <div class="web">www.clearframestudio.com</div>
    </div>
  </section>

  <section class="card card-front" aria-label="Card front">
    <div class="front-brand">
      <div class="plain-square"></div>
      <div>
        <div class="brand-name">Clear Frame Studio</div>
        <div class="brand-tagline">Architecture Corporate Commercial</div>
      </div>
    </div>

    <div class="person">
      <div class="person-name">Daniel Reyes</div>
      <div class="person-title">President</div>
      <address class="address">1420 Birchwood<br>Lane Juneau<br>Alaska 99801</address>
      <div class="web">www.clearframestudio.com</div>
    </div>

    <ul class="contacts">
      <li>Phone : 555-210-4418</li>
      <li>Mobile : 555-384-7720</li>
      <li>Fax : 555-602-1935</li>
      <li>Email : hello@clearframestudio.com</li>
    </ul>
  </section>
</body>
</html>
```